Road Construction Company needs business cards

We would like a new business card designed for our business.

We're a road construction company based in Qld, Australia.

Can the business card please have the following information on it.

Name: Warren Halbeck
Position: General Manager
Phone: 0472 915 348
Email: Warren.halbeck@tovrin.com.au
Address: 87 Marrow Ave, Pendlebay, QLD, 4023
Website: www.tovrin.com.au

Visually we'd like the card to be professional and simple.

Attached is our logo.

Our website is www.tovrin.com.au

Target Market(s)

Men aged 25-60

Contact Information for Business Card

As listed in project description

Font styles to use
Serif

Requirements
Must have
• Large logo on back of card

```html
<!DOCTYPE html>
<html lang="en">
<head>
<meta charset="utf-8">
<title>Tovrin Road Construction – Business Card</title>
<link rel="stylesheet" href="https://fonts.googleapis.com/css2?family=Noto+Serif:wght@400;700&display=swap">
<style>
  :root {
    --stage: #474747;
    --card-dark: #181818;
    --card-blue: #0657a7;
    --edge-blue: #35a5dd;
    --brand-blue: #0a5bb0;
    --light-blue: #36a6dd;
    --ink-white: #f2f2f2;
    --ghost-blue: #0d4f98;
  }
  * { margin: 0; padding: 0; box-sizing: border-box; }
  html, body {
    width: 1200px; height: 801px; overflow: hidden;
    background: var(--stage);
    font-family: "Noto Serif", Georgia, serif;
  }
  .stage {
    position: relative; width: 1200px; height: 801px;
  }
  .card {
    position: absolute; top: 235px;
    width: 540px; height: 330px;
    border-radius: 18px;
    border: 3px solid var(--edge-blue);
    overflow: hidden;
    box-shadow: 0 18px 30px rgba(0,0,0,.35);
  }
  .card-front { left: 30px; background: var(--card-dark); }
  .card-back { left: 630px; background: var(--card-blue); }

  /* front */
  .brand {
    position: absolute; top: 42px; left: 150px; width: 340px;
    color: var(--brand-blue); font-weight: 700; text-align: center;
  }
  .brand-name { display: block; font-size: 64px; line-height: 1; letter-spacing: 4px; }
  .brand-line { display: block; font-size: 17px; letter-spacing: 9px; margin-top: 8px; }

  .person { position: absolute; left: 52px; top: 158px; }
  .person-name { color: var(--light-blue); font-size: 25px; font-weight: 700; line-height: 1.1; }
  .person-role { color: var(--ink-white); font-size: 16px; margin-top: 3px; }

  .divider {
    position: absolute; left: 72px; right: 40px; top: 222px;
    height: 1.5px; background: var(--edge-blue);
  }
  .accent-square {
    position: absolute; left: 0; top: 212px;
    width: 30px; height: 30px; background: var(--light-blue);
  }

  .contacts { position: absolute; left: 60px; top: 236px; list-style: none; }
  .contacts li {
    display: flex; align-items: center; gap: 9px;
    color: var(--ink-white); font-size: 14.5px; line-height: 25px;
  }
  .contacts svg { width: 13px; height: 13px; fill: var(--light-blue); flex: none; }

  .address {
    position: absolute; right: 36px; top: 236px;
    color: var(--ink-white); font-size: 14.5px; line-height: 25px; font-style: normal;
  }

  /* back */
  .ghost-brand {
    position: absolute; top: 110px; left: 0; right: 0;
    color: var(--ghost-blue); font-weight: 700; text-align: center;
  }
  .ghost-brand .brand-name { font-size: 78px; letter-spacing: 6px; }
  .ghost-brand .brand-line { font-size: 19px; letter-spacing: 11px; }
</style>
</head>
<body>
<main class="stage">
  <section class="card card-front" aria-label="Business card front">
    <div class="brand">
      <span class="brand-name">TOVRIN</span>
      <span class="brand-line">ROAD CONSTRUCTION</span>
    </div>

    <div class="person">
      <p class="person-name">Warren Halbeck</p>
      <p class="person-role">General Manager</p>
    </div>

    <div class="accent-square"></div>
    <div class="divider"></div>

    <ul class="contacts">
      <li>
        <svg viewBox="0 0 24 24" aria-hidden="true"><path d="M6.6 10.8a15.1 15.1 0 0 0 6.6 6.6l2.2-2.2a1 1 0 0 1 1-.25 11.4 11.4 0 0 0 3.6.57 1 1 0 0 1 1 1V20a1 1 0 0 1-1 1A17 17 0 0 1 3 4a1 1 0 0 1 1-1h3.5a1 1 0 0 1 1 1c0 1.25.2 2.45.57 3.6a1 1 0 0 1-.25 1z"/></svg>
        0472 915 348
      </li>
      <li>
        <svg viewBox="0 0 24 24" aria-hidden="true"><path d="M2 5h20v14H2z M2 5l10 8 10-8" /></svg>
        Warren.halbeck@tovrin.com.au
      </li>
      <li>
        <svg viewBox="0 0 24 24" aria-hidden="true"><circle cx="12" cy="12" r="10"/></svg>
        www.tovrin.com.au
      </li>
    </ul>

    <address class="address">
      87 Marrow Ave,<br>
      Pendlebay, QLD, 4023
    </address>
  </section>

  <section class="card card-back" aria-label="Business card back">
    <div class="ghost-brand">
      <span class="brand-name">TOVRIN</span>
      <span class="brand-line">ROAD CONSTRUCTION</span>
    </div>
  </section>
</main>
</body>
</html>
```